business card for a massage therapy practice named 'Cedar and Willow Massage Studio'

I really need a trendy, yet easy on the eyes business card to complement my logo. Ideally with some gold or rose gold foil work.

My uploaded file of the logo I have in horizontal but I have a vertical version as well. Another color that is used in the website is a blush pink here and there. I'd like to see some trendy tropical leaves in the design.

```html
<!DOCTYPE html>
<html lang="en">
<head>
<meta charset="utf-8">
<title>Cedar and Willow Massage Studio – Business Card</title>
<link href="https://fonts.googleapis.com/css2?family=Questrial&family=Amatic+SC:wght@700&display=swap" rel="stylesheet">
<style>
  :root {
    --backdrop: #d9d9db;
    --card-black: #121213;
    --card-white: #f7f7f5;
    --gold: #9c8655;
    --gold-soft: #b9a67a;
    --mint: #79c2ab;
    --ink: #1b1b1b;
    --grey: #8a8a8a;
    --white: #ffffff;
  }
  * { margin: 0; padding: 0; box-sizing: border-box; }
  html, body {
    width: 1200px;
    height: 857px;
    overflow: hidden;
    background: var(--backdrop);
    font-family: "Questrial", sans-serif;
  }
  .sheet {
    width: 1200px;
    height: 857px;
    display: flex;
    align-items: center;
    justify-content: center;
    gap: 48px;
  }
  .card {
    position: relative;
    width: 530px;
    height: 303px;
    overflow: hidden;
    box-shadow: 0 6px 18px rgba(0,0,0,0.18);
  }

  /* Front */
  .card--front {
    background: var(--card-black);
    display: flex;
    flex-direction: column;
    align-items: center;
    justify-content: center;
  }
  .brand {
    display: flex;
    align-items: center;
    gap: 18px;
  }
  .brand__dot {
    width: 46px;
    height: 46px;
    border-radius: 50%;
    background: var(--gold);
    flex-shrink: 0;
  }
  .brand__name {
    color: var(--white);
    font-size: 30px;
    line-height: 1.15;
    letter-spacing: 1px;
  }
  .brand__name span { display: block; }
  .front__web {
    margin-top: 44px;
    color: var(--white);
    font-size: 15px;
    letter-spacing: 1px;
  }

  /* Back */
  .card--back {
    background: var(--card-white);
    padding: 34px 40px;
  }
  .brand--small { gap: 12px; }
  .brand--small .brand__dot { width: 28px; height: 28px; }
  .brand--small .brand__name {
    color: var(--ink);
    font-size: 18px;
  }
  .person {
    margin-top: 40px;
  }
  .person__name {
    font-family: "Amatic SC", cursive;
    font-weight: 700;
    color: var(--gold);
    font-size: 30px;
    letter-spacing: 1px;
  }
  .person__role {
    color: var(--grey);
    font-size: 13px;
    letter-spacing: 1px;
    margin-top: 2px;
  }
  .contact {
    margin-top: 26px;
    list-style: none;
    font-size: 13px;
    line-height: 1.55;
    color: var(--grey);
  }
  .contact__label { color: var(--gold); }
  .leaf-decoration {
    position: absolute;
    top: 0;
    right: 0;
    width: 120px;
    height: 100%;
    background: linear-gradient(90deg, rgba(156,134,85,0) 0%, rgba(156,134,85,0.55) 55%, var(--gold-soft) 100%);
  }
</style>
</head>
<body>
  <main class="sheet">
    <section class="card card--front" aria-label="Card front">
      <div class="brand">
        <div class="brand__dot"></div>
        <div class="brand__name">
          <span>Cedar and Willow</span>
          <span>Massage Studio</span>
        </div>
      </div>
      <p class="front__web">www.cedarwillow.com</p>
    </section>

    <section class="card card--back" aria-label="Card back">
      <div class="brand brand--small">
        <div class="brand__dot"></div>
        <div class="brand__name">
          <span>Cedar and Willow</span>
          <span>Massage Studio</span>
        </div>
      </div>
      <div class="person">
        <p class="person__name">Mara Ellis</p>
        <p class="person__role">Artist</p>
      </div>
      <ul class="contact">
        <li><span class="contact__label">Phone:</span> +123 555 017 0</li>
        <li><span class="contact__label">Email:</span> hello@cedarwillow.com</li>
        <li><span class="contact__label">Web:</span> www.cedarwillow.com</li>
      </ul>
      <div class="leaf-decoration" role="img" aria-label="Gold foil tropical fruit and leaf decoration along the right edge"></div>
    </section>
  </main>
</body>
</html>
```